Tech business card design

We need an amazing business card design for our new business 'Pexla' a marketing tech startup based in Sydney, Australia. We provide an online marketplace for businesses to search and buy advertising media, connect with service providers and learn more about marketing. We wish to communicate 'cool tech', reliability and professionalism and design based around our logo.

Target Market(s)

Business Owners

Contact Information for Business Card

Name
Position
Email Address
Website
Phone Number

Font styles to use
Other font styles liked:
• Avenir & Avenir Next

Colors

Designer to choose colors to be used in the design.

```html
<!DOCTYPE html>
<html lang="en">
<head>
<meta charset="utf-8">
<title>Pexla Business Card</title>
<link rel="stylesheet" href="https://fonts.googleapis.com/css2?family=Source+Sans+3:wght@400;600;700;900&display=swap">
<style>
  :root {
    --backdrop: #93a9b5;
    --card: #b6b6b6;
    --card-edge: #4a4a4a;
    --ink: #2b2b2b;
    --ink-soft: #3a3a3a;
    --rule: #5a5a5a;
    --icon-blue: #1b5db0;
    --brand-navy: #0f0e36;
  }
  * { margin: 0; padding: 0; box-sizing: border-box; }
  html, body {
    width: 1082px; height: 1200px; overflow: hidden;
    background: var(--backdrop);
    font-family: "Source Sans 3", "Helvetica Neue", Arial, sans-serif;
    color: var(--ink);
  }
  .canvas { position: relative; width: 1082px; height: 1200px; }
  .card {
    position: absolute; left: 84px; width: 914px; height: 522px;
    background: radial-gradient(ellipse at 50% 40%, #bcbcbc 0%, var(--card) 60%, #aeaeae 100%);
    border-top: 1px solid var(--card-edge);
  }
  .card--front { top: 37px; }
  .card--back { top: 619px; }
  .centered { position: absolute; left: 0; right: 0; text-align: center; line-height: 1; }
  .person-name { top: 180px; font-size: 33px; font-weight: 700; letter-spacing: 0.2px; color: #262626; }
  .person-role { top: 213px; font-size: 28px; font-weight: 400; color: var(--ink-soft); }
  .divider { position: absolute; top: 261px; left: 248px; width: 418px; height: 1px; background: var(--rule); }
  .contact-row { display: flex; justify-content: center; align-items: center; gap: 18px; color: var(--ink-soft); }
  .contact-row--primary { top: 319px; font-size: 26px; }
  .contact-row--web { top: 362px; font-size: 23px; letter-spacing: 3.5px; }
  .contact-item { display: inline-flex; align-items: center; gap: 9px; }
  .contact-item svg { width: 24px; height: 24px; fill: none; stroke: var(--icon-blue); stroke-width: 1.8; }
  .address { top: 409px; font-size: 25px; color: var(--ink-soft); }
  .brand-name { top: 178px; font-size: 190px; font-weight: 900; color: var(--brand-navy); letter-spacing: -2px; }
  .brand-site { top: 424px; font-size: 30px; letter-spacing: 4px; color: var(--ink-soft); }
</style>
</head>
<body>
<main class="canvas">
  <section class="card card--front">
    <h1 class="centered person-name">JOHN SMITH</h1>
    <p class="centered person-role">Position</p>
    <div class="divider"></div>
    <div class="centered contact-row contact-row--primary">
      <span class="contact-item">
        <svg viewBox="0 0 24 24" aria-hidden="true"><circle cx="12" cy="12" r="10"/><path d="M9 7c-2 3-2 7 1 10l2-2-2-2c0-2 1-3 2-4l-3-2z"/></svg>
        012-345-6789
      </span>
      <span class="contact-item">
        <svg viewBox="0 0 24 24" aria-hidden="true"><rect x="2" y="5" width="20" height="14" fill="var(--icon-blue)" stroke="none"/><path d="M2 5l10 8 10-8M2 19l7-7M22 19l-7-7" stroke="#d8e4f4"/></svg>
        info@pexla.com
      </span>
    </div>
    <div class="centered contact-row contact-row--web">
      <span class="contact-item">
        <svg viewBox="0 0 24 24" aria-hidden="true"><circle cx="12" cy="12" r="10"/><ellipse cx="12" cy="12" rx="4.5" ry="10"/><path d="M2 12h20M4 7h16M4 17h16"/></svg>
        www.pexla.com
      </span>
    </div>
    <p class="centered address">Street name City Name, Zipcode,012345</p>
  </section>

  <section class="card card--back">
    <p class="centered brand-name">pexla</p>
    <p class="centered brand-site">www.pexla.com</p>
  </section>
</main>
</body>
</html>
```